Building company buisness cards

We are looking for a sharp modern new look for our business cards.
We are a New Zealand based company that specialises in house and land packages.
We have attached a photo of the current logo and would like to see if it can be improved somehow if needed.
We are open to any colours but we have chosen green at this stage.
Feel free to change the font and make the logo smarter looking.
Play with the colours and see what looks best.

We want a card that looks so good know one will want to throw it away!

Target Market(s)

Home buyers

Industry/Entity Type

Building

Contact Information for Business Card

Derek Tolvane
0217394062
dtolvane@quillmarkhomesteads.co.nz
quillmarkhomesteads.co.nz

Font styles to use
Serif
Sans Serif

Colors

Designer to choose colors to be used in the design.

Requirements
Must have
• Logo and company name on one side, details on the other side
Nice to have
• Color codes for the original green are HEX #4a8028, RGB(74,128,40), CMYK(42,0,69,50)
• Round corners, Raised and/or spot UV

```html
<!DOCTYPE html>
<html lang="en">
<head>
<meta charset="utf-8">
<title>Quillmark Homesteads — Business Cards</title>
<link rel="stylesheet" href="https://fonts.googleapis.com/css2?family=Montserrat:wght@400;500;600;800;900&display=swap">
<style>
  :root {
    --brand-green: #4a8028;
    --brand-green-light: #5a9040;
    --card-white: #ffffff;
    --soft-grey: #eeeeee;
    --pale-green: #dfe9d8;
    --ink: #2b2b2b;
    --backdrop: #2a2a2a;
  }
  * { box-sizing: border-box; margin: 0; padding: 0; }
  html, body { width: 1200px; height: 897px; overflow: hidden; }
  body {
    background: var(--backdrop);
    font-family: "Montserrat", Arial, sans-serif;
    position: relative;
  }
  .card {
    position: absolute;
    left: 303px;
    width: 595px;
    height: 338px;
    border-radius: 18px;
    overflow: hidden;
    background: var(--card-white);
    box-shadow: 0 8px 18px rgba(0,0,0,0.45);
  }
  .card--details { top: 92px; }
  .card--brand { top: 470px; }

  .card__band {
    position: absolute; left: 0; top: 0; width: 100%;
    background: linear-gradient(120deg, var(--brand-green) 40%, var(--brand-green-light) 100%);
  }
  .card--details .card__band { height: 218px; }
  .card--brand .card__band { height: 160px; background: var(--brand-green); }

  .illustration {
    position: absolute;
    border-radius: 22px 22px 0 0;
  }
  .illustration--front {
    left: 330px; top: 116px; width: 250px; height: 210px;
    background: linear-gradient(180deg, var(--card-white) 0%, var(--card-white) 45%, var(--pale-green) 100%);
  }
  .illustration--back {
    left: 135px; top: 32px; width: 330px; height: 128px;
    background: linear-gradient(180deg, var(--card-white) 0%, var(--soft-grey) 100%);
  }

  .wordmark {
    position: absolute;
    font-weight: 800;
    letter-spacing: -1px;
    line-height: 1;
    text-align: center;
  }
  .wordmark span { display: block; }
  .wordmark--small {
    left: 24px; top: 80px; width: 250px;
    color: var(--card-white);
  }
  .wordmark--small .wordmark__top { font-size: 22px; }
  .wordmark--small .wordmark__bottom { font-size: 28px; margin-top: 3px; }

  .person {
    position: absolute; right: 31px; top: 24px;
    text-align: right; color: var(--card-white);
  }
  .person__name { font-weight: 600; font-size: 21px; }
  .person__role { font-weight: 400; font-size: 16px; margin-top: 1px; }

  .contacts {
    position: absolute; left: 29px; top: 253px;
    list-style: none; color: var(--ink);
    font-size: 14.5px; font-weight: 400;
  }
  .contacts li { display: flex; align-items: center; height: 19px; }
  .contacts svg { width: 10px; height: 10px; margin-right: 7px; flex: none; }

  .wordmark--large {
    left: 0; width: 100%; top: 172px;
    color: var(--brand-green);
  }
  .wordmark--large .wordmark__top { font-size: 40px; }
  .wordmark--large .wordmark__bottom { font-size: 52px; margin-top: 2px; }

  .brand-url {
    position: absolute; left: 0; width: 100%; top: 297px;
    text-align: center; color: var(--brand-green);
    font-size: 15px; font-weight: 400;
  }
</style>
</head>
<body>
  <section class="card card--details">
    <div class="card__band"></div>
    <div class="illustration illustration--front" role="img" aria-label="Illustration of a family sheltered under a house roof"></div>
    <div class="wordmark wordmark--small"><span class="wordmark__top">quillmark</span><span class="wordmark__bottom">homesteads.</span></div>
    <div class="person">
      <div class="person__name">Derek Tolvane</div>
      <div class="person__role">Founder</div>
    </div>
    <ul class="contacts">
      <li>
        <svg viewBox="0 0 10 10" aria-hidden="true"><path d="M2 1 L3.6 1 L4.2 3 L3.2 3.8 Q4 5.8 6.2 6.8 L7 5.8 L9 6.4 L9 8 Q8.6 9 7.4 9 Q1 8 1 2.4 Q1 1 2 1 Z" fill="var(--brand-green)"/></svg>
        0217394062
      </li>
      <li>
        <svg viewBox="0 0 10 10" aria-hidden="true"><rect x="0.7" y="2" width="8.6" height="6.2" rx="0.8" fill="none" stroke="var(--brand-green)" stroke-width="1.2"/><path d="M1 2.5 L5 5.6 L9 2.5" fill="none" stroke="var(--brand-green)" stroke-width="1.2"/></svg>
        dtolvane@quillmarkhomesteads.co.nz
      </li>
      <li>
        <svg viewBox="0 0 10 10" aria-hidden="true"><circle cx="5" cy="5" r="4.2" fill="none" stroke="var(--brand-green)" stroke-width="1.1"/><ellipse cx="5" cy="5" rx="1.8" ry="4.2" fill="none" stroke="var(--brand-green)" stroke-width="1"/><path d="M0.8 5 H9.2 M1.5 3 H8.5 M1.5 7 H8.5" stroke="var(--brand-green)" stroke-width="0.9"/></svg>
        quillmarkhomesteads.co.nz
      </li>
    </ul>
  </section>

  <section class="card card--brand">
    <div class="card__band"></div>
    <div class="illustration illustration--back" role="img" aria-label="Large faint illustration of a house roof over a family"></div>
    <div class="wordmark wordmark--large"><span class="wordmark__top">quillmark</span><span class="wordmark__bottom">homesteads.</span></div>
    <div class="brand-url">quillmarkhomesteads.co.nz</div>
  </section>
</body>
</html>
```